Diverse, up-scale salon needs eye-catching, unique business cards.

We are looking for a unique business card design for our stylist but that can also be multi functional and used for appointment reminder and referrals. I will need a design in a format that I can modify names and titles going forward. In the past we have had a dark background with the logo on one side, and stylist and contact information on the other but we are open to all ideas. I have included our mission statement as well as branded colors below. The statement doesn't need to go on the card, it's just a reference for target market. We need space for the stylists name, title, instagram handle and then the salons phone number, website and address. I am also open to adding a spot for a qr code linked to the stylist instagram or the salon booking link.

primary brand colors:
#333333 #233415 #36502a #93874a #000000
Mission statement:
Vessolin Hair Studio, a high-end salon located in the lively Downtown Farmington, Michigan, is committed to providing exceptional services in a welcoming and relaxed environment to meet the needs of our diverse clientele.
Our salon specializes in contemporary custom haircuts, coloring, extensions, and barbering and beard grooming services. Our team of skilled stylists is passionate and inventive in their hair styling techniques. At the heart of our salon are values centered on quality, innovation, creativity, and above all, comfort. These core values are evident in every appointment across our customizable array of services.
Our goal is to establish a benchmark for exceptional hair care for every human.
Website: www.vessolinhairstudio.example
instagram: @vessolinhairstudio
address: 41782 Pelham Crest Rd, Farmington MI
phone: 248-613-4087

Industry/Entity Type

Hair Salon

Contact Information for Business Card

Stylist name, title, phone, instagram, website, address, (optional qr code)

Requirements
Should not have
• Does not need mission statement on the card.

```html
<!DOCTYPE html>
<html lang="en">
<head>
<meta charset="utf-8">
<title>Vessolin Hair Studio – Business Card</title>
<link href="https://fonts.googleapis.com/css2?family=Arimo:wght@400;700&display=swap" rel="stylesheet">
<style>
  :root {
    --backdrop: #1a1a1a;
    --ink: #000000;
    --paper: #ffffff;
    --muted: #8a8a8a;
  }
  * { margin: 0; padding: 0; box-sizing: border-box; }
  html, body {
    width: 1200px; height: 1059px; overflow: hidden;
    background: var(--backdrop);
    font-family: "Arimo", Arial, sans-serif;
  }
  .card { position: absolute; overflow: hidden; }

  /* Front side */
  .card-front {
    left: 258px; top: 89px; width: 689px; height: 394px;
    background: var(--paper);
  }
  .name-band {
    position: absolute; left: 0; top: 66px; width: 100%; height: 88px;
    background: var(--ink);
  }
  .stylist-name {
    position: absolute; left: 36px; top: 87px;
    color: var(--paper); font-weight: 700; font-size: 20px; letter-spacing: 0.2px;
  }
  .stylist-title {
    position: absolute; left: 36px; top: 111px;
    color: var(--paper); font-size: 17px;
  }
  .brand-seal {
    position: absolute; left: 443px; top: 27px; width: 162px; height: 162px;
    border-radius: 50%; background: var(--paper);
    display: flex; align-items: center; justify-content: center; text-align: center;
  }
  .brand-seal-name {
    font-weight: 700; font-size: 17px; line-height: 1.2; color: var(--ink);
    text-transform: uppercase; letter-spacing: 1px;
  }
  .contact-list {
    position: absolute; left: 35px; top: 272px; list-style: none;
  }
  .contact-item {
    display: flex; align-items: center; height: 28.5px;
    color: var(--muted); font-size: 19px;
  }
  .contact-icon { width: 16px; height: 16px; margin-right: 10px; flex: none; }
  .address {
    position: absolute; right: 39px; top: 304px; text-align: right;
    color: var(--muted); font-size: 19px; line-height: 25px;
  }

  /* Back side */
  .card-back {
    left: 252px; top: 541px; width: 701px; height: 400px;
    background: var(--ink); color: var(--paper);
  }
  .services-heading {
    position: absolute; left: 43px; top: 52px;
    font-weight: 700; font-size: 21px;
  }
  .services-list {
    position: absolute; left: 47px; top: 84px; list-style: none;
  }
  .services-list li {
    font-size: 21px; line-height: 27px; display: flex; align-items: center;
  }
  .services-list li::before {
    content: ""; width: 8px; height: 8px; border-radius: 50%;
    background: var(--paper); margin-right: 7px;
  }
  .brand-ring {
    position: absolute; left: 390px; top: 65px; width: 252px; height: 252px;
    border: 3px solid var(--paper); border-radius: 50%;
    display: flex; align-items: center; justify-content: center; text-align: center;
  }
  .brand-ring-name {
    font-weight: 700; font-size: 26px; line-height: 1.25; color: var(--paper);
    text-transform: uppercase; letter-spacing: 2px;
  }
</style>
</head>
<body>

<section class="card card-front">
  <div class="name-band"></div>
  <p class="stylist-name">MARCUS DELANEY</p>
  <p class="stylist-title">Manager</p>
  <div class="brand-seal"><span class="brand-seal-name">Vessolin<br>Hair Studio</span></div>

  <ul class="contact-list">
    <li class="contact-item">
      <svg class="contact-icon" viewBox="0 0 24 24" aria-hidden="true">
        <path d="M6.6 3.5l3 3-2 2.3c1.2 2.5 3.1 4.4 5.6 5.6l2.3-2 3 3-2.2 2.4C11 17.5 6.5 13 4.2 5.7z" fill="#000"/>
      </svg>248-613-4087
    </li>
    <li class="contact-item">
      <svg class="contact-icon" viewBox="0 0 24 24" aria-hidden="true">
        <circle cx="12" cy="12" r="9" fill="none" stroke="#000" stroke-width="2.5"/>
      </svg>@vessolinhairstudio
    </li>
    <li class="contact-item">
      <svg class="contact-icon" viewBox="0 0 24 24" aria-hidden="true" fill="none" stroke="#000" stroke-width="1.6">
        <circle cx="12" cy="12" r="10"/>
        <ellipse cx="12" cy="12" rx="4.5" ry="10"/>
        <line x1="2" y1="12" x2="22" y2="12"/>
        <line x1="4" y1="7" x2="20" y2="7"/>
        <line x1="4" y1="17" x2="20" y2="17"/>
      </svg>www.vessolinhairstudio.example
    </li>
  </ul>

  <p class="address">41782 Pelham Crest Rd<br>Farmington MI</p>
</section>

<section class="card card-back">
  <h2 class="services-heading">OUR SERVICES</h2>
  <ul class="services-list">
    <li>Custom Haircuts</li>
    <li>Coloring</li>
    <li>Extensions</li>
    <li>And Barbering</li>
    <li>Beard Grooming</li>
  </ul>
  <div class="brand-ring"><span class="brand-ring-name">Vessolin<br>Hair Studio</span></div>
</section>

</body>
</html>
```